Website for Plumbing Company, Mr. FlowKettle

I need a 7-page fully HTML-coded website for my plumbing company, Mr. FlowKettle. We specialize in installation, repair, and replacement of both gas and electric water heaters. Although we offer both tankless (on-demand) water heaters and standard (with tank) water heaters, most of our business is related to standard (with tank) water heaters in the USA market.

These are the pages I need:
1. Home page with sections such as About Us, Our Services, Why Choose Us, Testimonials, Location Map (Palm Beach County Florida), Quote Request Form, Join Our Newsletter, Mission Statement, etc.

2. Gas Water Heaters

3. Electric Water Heaters

4. Tankless Water Heaters

5. About Us

6. Contact Us

7. Privacy Policy, Terms & Conditions

Be sure to mention the following points:
1. Same-Day Service
2. Best Price Guarantee
3. 100% Satisfaction Rating
4. 15-Year Warranty on Water Heater & Parts
5. Lifetime Warranty on Workmanship
*All Warranties are Transferrable Upon Home Sale

Once design is selected and finalized, I need the website coded in a standard HTML/CSS and temporarily hosted on your development server so I can see the website functionality that is not observable from screenshots, such as section animations, etc. Once those details are finalized, I will move the source code to my server and complete the project.

Residential Home Owners and Business Owners

Plumbing, Home Services, Remodeling, Construction

0054AA
0677BA
7BADD7
CADEEF
E8F1F8
FFC000
F8CF3A
FAE287
FDF2CF
FEFAEE
EE7325
F08F49
F5BC92
FAE3D3
FDF4ED

• Clean, colorful, and professional

```html
<!DOCTYPE html>
<html lang="en">
<head>
<meta charset="utf-8">
<title>Mr. FlowKettle — Home</title>
<link href="https://fonts.googleapis.com/css2?family=Lilita+One&family=Roboto:wght@400;500;700&display=swap" rel="stylesheet">
<style>
:root{
  --blue:#0054AA;
  --blue-mid:#0677BA;
  --blue-deep:#0e3f95;
  --navy:#1b3f8f;
  --sky:#7BADD7;
  --orange:#EE7325;
  --orange-soft:#F08F49;
  --yellow:#FFC000;
  --ink:#222;
  --text:#5a5a5a;
  --line:#c9c9c9;
  --white:#fff;
}
*{box-sizing:border-box;margin:0;padding:0}
html,body{width:1200px;height:4781px;overflow:hidden}
body{position:relative;font-family:"Roboto",Arial,sans-serif;color:var(--ink);background:var(--white)}
.abs{position:absolute}
.display{font-family:"Lilita One","Arial Black",sans-serif;font-weight:400;letter-spacing:.5px}
.display .b{color:var(--blue)} .display .o{color:var(--orange)}
.section-title{font-size:56px;line-height:1;white-space:nowrap}
.brand-name{font-family:"Roboto",Arial,sans-serif;font-weight:700;white-space:nowrap;line-height:1}
.lead{font-size:14px;line-height:26px;color:var(--text)}
.btn{position:absolute;display:flex;align-items:center;justify-content:center;gap:6px;font-size:13px;font-weight:700;border-radius:4px;text-transform:uppercase}
.btn-blue{background:var(--blue);color:#fff;box-shadow:0 3px 6px rgba(0,0,0,.25)}
.bg-band{position:absolute;left:0;width:1200px}

/* header */
.logo-blob{left:0;top:0;width:232px;height:195px;background:#fff;border-radius:0 0 120px 60px;box-shadow:0 4px 10px rgba(0,0,0,.15);display:flex;align-items:center;justify-content:center;z-index:5}
.logo-blob span{font-weight:700;font-size:23px;color:var(--blue)}
.topbar{left:0;top:0;width:1200px;height:80px;background:#fff;z-index:4}
.nav{left:230px;top:28px;display:flex;gap:20px;font-size:14px;color:#222;z-index:5}
.nav .active{color:var(--blue);border-bottom:2px solid var(--blue);padding-bottom:4px}
.call{right:0;top:0;width:250px;height:80px;z-index:5}
.call-text{right:8px;top:16px;color:#fff;z-index:6}
.call-text small{display:block;font-size:13px}
.call-text b{font-size:22px}

/* hero */
.hero-photo{left:0;top:80px;width:1200px;height:720px;background:linear-gradient(100deg,#3b3a38 0%,#6d6a66 30%,#9c948a 55%,#6b5c4c 80%,#4a3f35 100%)}
.hero-title{left:204px;top:300px;font-size:66px;color:#fff;text-shadow:0 4px 10px rgba(0,0,0,.4)}
.btn-white{background:#fff;color:#111}
.btn-orange{background:var(--orange);color:#fff}
.scroll-down{left:576px;top:576px;width:48px;height:48px;border:2px solid #fff;border-radius:50%}

/* about */
.kicker{left:0;width:1200px;top:798px;text-align:center;font-size:17px;letter-spacing:6px;color:var(--blue)}
.illus{left:130px;top:927px;width:449px;height:242px;border-radius:20px;background:radial-gradient(ellipse at 40% 45%,#d9e6f5 0%,#9fc0e6 55%,#fff 80%)}

/* services */
.card{position:absolute;top:1549px;width:315px;height:293px;border:4px solid #e2e2e2;border-radius:14px;background:#ddd}
.card-label{position:absolute;top:1856px;width:315px;text-align:center;font-size:20px;font-weight:500;color:#222}
.arrow{position:absolute;top:1610px}

/* why */
.why-circle{position:absolute;top:2717px;width:252px;height:252px;border-radius:50%;background:#fff;border:8px solid #9ebfe6;text-align:center;padding:40px 26px 0}
.why-circle h3{font-size:18px;font-weight:700;line-height:26px;color:#222;margin-top:10px}
.why-circle p{font-size:13px;line-height:20px;color:var(--text);margin-top:6px}

/* form */
.field{position:absolute;border:1.5px solid #bbb;background:#fff;font-size:13px;color:#444;padding:15px 18px}

/* footer */
.foot-h{font-size:20px;font-weight:700;color:#fff}
.foot-links{list-style:none;font-size:14px;color:#fff;line-height:26px}
.foot-links li::before{content:"»";margin-right:18px}
.foot-icon{position:absolute;width:40px;height:40px;border-radius:50%;background:var(--orange);display:flex;align-items:center;justify-content:center}
.foot-text{position:absolute;width:300px;left:450px;text-align:center;color:#fff;font-size:14px;line-height:26px}
.social{position:absolute;top:4611px;width:32px;height:32px;border-radius:50%;border:1.5px solid #fff}
</style>
</head>
<body>

<!-- HERO -->
<div class="abs hero-photo" role="img" aria-label="Technician with arms crossed standing in a warehouse beside tank and tankless water heaters"></div>
<svg class="abs" style="left:0;top:600px" width="1200" height="220" viewBox="0 0 1200 220">
  <polygon points="0,140 400,40 400,60 0,200" fill="var(--orange)"/>
  <polygon points="700,80 1200,100 1200,180 900,130" fill="var(--yellow)"/>
  <polygon points="0,200 400,40 1200,150 1200,220 0,220" fill="#fff"/>
</svg>
<div class="abs topbar"></div>
<div class="abs logo-blob"><span>Mr. FlowKettle</span></div>
<nav class="abs nav">
  <span class="active">Home</span><span>About us</span><span>Gas Water Heaters</span><span>Electric Water Heaters</span><span>Tankless Water Heaters</span><span>Contact us</span>
</nav>
<svg class="abs call" width="250" height="80" viewBox="0 0 250 80">
  <polygon points="0,80 40,0 250,0 250,80" fill="var(--orange)"/>
  <polygon points="18,80 52,0 250,0 250,80" fill="var(--blue)"/>
  <path d="M62 28c3 9 9 15 18 19l5-5-8-4-4 3c-4-2-7-5-9-9l3-4-4-8z" fill="#fff"/>
</svg>
<div class="abs call-text"><small>Call us Today :</small><b>+1 888 888 8888</b></div>

<h1 class="abs hero-title brand-name">Mr. FlowKettle</h1>
<div class="btn btn-white" style="left:210px;top:445px;width:157px;height:47px">
  <svg width="12" height="12" viewBox="0 0 24 24"><path d="M4 3c2 9 8 15 17 17l1-5-6-2-3 3c-3-1-6-4-7-7l3-3-2-6z" fill="var(--blue)"/></svg>Contact Us</div>
<div class="btn btn-orange" style="left:380px;top:445px;width:134px;height:47px">Book Now</div>
<svg class="abs scroll-down" viewBox="0 0 48 48"><path d="M16 20l8 8 8-8" stroke="#fff" stroke-width="2" fill="none"/></svg>

<!-- ABOUT -->
<div class="abs kicker">ABOUT US</div>
<h2 class="abs brand-name" style="left:0;width:1200px;top:836px;text-align:center;font-size:46px;color:var(--blue)">Mr. FlowKettle</h2>
<div class="abs illus" role="img" aria-label="Cartoon mascot plumber carrying a water heater tank"></div>
<div class="abs lead" style="left:601px;top:914px;width:490px">
  <p>Lorem ipsum dolor sit amet, consectetur adipiscing elit, sed do eiusmod tempor incididunt ut labore et dolore magna aliqua. Ut enim ad minim veniam, quis nostrud exercitation ullamco laboris nisi ut aliquip ex ea commodo consequat.</p>
  <p style="margin-top:24px">Duis aute irure dolor in reprehenderit in voluptate velit esse cillum dolore eu fugiat nulla pariatur. Excepteur sint occaecat cupidatat non proident, sunt in culpa qui officia deserunt mollit anim id est laborum.</p>
</div>
<div class="btn btn-blue" style="left:601px;top:1150px;width:148px;height:50px">Learn More ›</div>

<!-- SERVICES BAND -->
<svg class="bg-band" style="top:1210px" width="1200" height="530" viewBox="0 0 1200 530">
  <defs><linearGradient id="gBlue" x1="0" y1="0" x2="1" y2="1"><stop offset="0" stop-color="#0e4ea6"/><stop offset="1" stop-color="#1b5fb8"/></linearGradient></defs>
  <rect x="0" y="0" width="1200" height="524" fill="url(#gBlue)"/>
  <polygon points="0,0 1200,0 1200,10 835,166 0,40" fill="var(--orange)"/>
  <polygon points="0,0 1200,0 1200,30 835,166 0,72" fill="#fff"/>
  <polygon points="835,166 1200,10 1200,30" fill="var(--yellow)"/>
</svg>
<div class="abs display section-title" style="left:0;width:1200px;top:1465px;text-align:center"><span style="color:#fff">What </span><span class="o">We Do</span></div>
<svg class="arrow" style="left:34px" width="44" height="24" viewBox="0 0 44 24"><path d="M42 12H4M14 2L4 12l10 10" stroke="#fff" stroke-width="3" fill="none"/></svg>
<svg class="arrow" style="left:1122px" width="44" height="24" viewBox="0 0 44 24"><path d="M2 12h38M30 2l10 10-10 10" stroke="#fff" stroke-width="3" fill="none"/></svg>
<div class="card" style="left:108px;background:linear-gradient(120deg,#c9c2b8,#e9e4de 50%,#777 100%)" role="img" aria-label="Technician working on a wall-mounted gas water heater"></div>
<div class="card" style="left:445px;background:linear-gradient(150deg,#e8e6e0,#c8a890 50%,#b33 90%)" role="img" aria-label="Plumber connecting an electric water heater"></div>
<div class="card" style="left:779px;background:linear-gradient(100deg,#6b5848,#b8b6b2 45%,#8a7a68 100%)" role="img" aria-label="Tankless water heater mounted on a wall"></div>
<div class="card-label" style="left:108px">Gas Water Heaters</div>
<div class="card-label" style="left:445px;color:var(--orange);text-decoration:underline">Electric Water Heaters</div>
<div class="card-label" style="left:779px">Tankless Water Heaters</div>

<!-- MISSION -->
<div class="abs display section-title" style="left:108px;top:2005px"><span class="b">Our </span><span class="o">Mission</span></div>
<div class="abs lead" style="left:111px;top:2073px;width:488px;text-align:justify;font-size:13.5px;line-height:21.5px">
  <p>Lorem ipsum dolor sit amet, consectetur adipiscing elit, sed do eiusmod tempor incididunt ut labore et dolore magna aliqua. Ut enim ad minim veniam, quis nostrud exercitation ullamco laboris nisi ut aliquip ex ea commodo consequat. Duis aute irure dolor in reprehenderit in voluptate velit esse cillum dolore eu fugiat nulla pariatur. Excepteur sint occaecat cupidatat sunt in culpa qui officia deserunt mollit anim id est laborum. Lorem ipsum dolor sit amet, consectetur adipiscing elit, sed do eiusmod tempor incididunt ut labore et dolore magna aliqua.</p>
  <p style="margin-top:21px">Ut enim ad minim veniam, quis nostrud exercitation ullamco laboris nisi ut aliquip ex ea commodo consequat. Duis aute irure dolor in reprehenderit in voluptate velit esse cillum dolore eu fugiat nulla pariatur.</p>
</div>
<div class="btn btn-blue" style="left:111px;top:2341px;width:165px;height:50px">Learn More ›</div>
<svg class="abs" style="left:630px;top:1966px" width="464" height="464" viewBox="0 0 464 464">
  <circle cx="232" cy="232" r="226" fill="none" stroke="var(--blue)" stroke-width="4"/>
  <path d="M232 6a226 226 0 0 1 226 226" fill="none" stroke="var(--orange)" stroke-width="5"/>
  <circle cx="232" cy="232" r="206" fill="var(--orange)"/>
  <circle cx="232" cy="232" r="200" fill="#b9c6d6"/>
</svg>
<div class="abs" style="left:662px;top:1998px;width:400px;height:400px;border-radius:50%;background:linear-gradient(110deg,#e8edf3 0%,#9fb2c8 40%,#c43a2e 70%,#2b4d8e 100%)" role="img" aria-label="Smiling technician in overalls standing in front of a service van"></div>
<svg class="abs" style="left:938px;top:2300px" width="104" height="104" viewBox="0 0 104 104">
  <circle cx="52" cy="52" r="50" fill="var(--blue)" stroke="#fff" stroke-width="4"/>
  <path d="M44 38v28l22-14z" fill="#fff"/>
</svg>

<!-- WHY CHOOSE -->
<svg class="bg-band" style="top:2532px" width="1200" height="700" viewBox="0 0 1200 700">
  <defs><linearGradient id="gWhy" x1="0" y1="0" x2="1" y2="1"><stop offset="0" stop-color="#123f9a"/><stop offset="1" stop-color="#1c5cb6"/></linearGradient></defs>
  <rect width="1200" height="700" fill="url(#gWhy)"/>
  <polygon points="0,660 779,528 1200,630 1200,700 0,700" fill="var(--orange)"/>
  <polygon points="779,528 1200,600 1200,700" fill="var(--yellow)"/>
  <polygon points="0,700 0,690 779,528 1200,670 1200,700" fill="#fff"/>
</svg>
<div class="abs display section-title" style="left:0;width:1200px;top:2628px;text-align:center"><span style="color:#fff">Why </span><span class="o">Choose Us</span></div>

<div class="why-circle" style="left:106px">
  <svg width="56" height="56" viewBox="0 0 56 56"><path d="M6 30l12-12 10 6 10-6 12 12-14 14-8-6-8 6z" fill="none" stroke="var(--orange)" stroke-width="2.5"/><path d="M28 6v8M20 9l3 6M36 9l-3 6" stroke="var(--orange)" stroke-width="2.5"/></svg>
  <h3>Same-Day Service</h3><p>Lorem ipsum dolor sit amet, consectetur adipiscing elitdo eiusmod tempor</p>
</div>
<div class="why-circle" style="left:351px">
  <svg width="56" height="56" viewBox="0 0 56 56"><circle cx="32" cy="22" r="14" fill="none" stroke="var(--orange)" stroke-width="2.5"/><path d="M32 14v16M28 18h7M28 26h7" stroke="var(--orange)" stroke-width="2.5"/><rect x="8" y="38" width="26" height="12" rx="3" fill="none" stroke="var(--orange)" stroke-width="2.5"/></svg>
  <h3>Best Price Guarantee</h3><p>Lorem ipsum dolor sit amet, consectetur adipiscing elitdo eiusmod tempor</p>
</div>
<div class="why-circle" style="left:596px">
  <svg width="56" height="56" viewBox="0 0 56 56"><circle cx="28" cy="16" r="7" fill="none" stroke="var(--orange)" stroke-width="2.5"/><circle cx="12" cy="22" r="5" fill="none" stroke="var(--orange)" stroke-width="2.5"/><circle cx="44" cy="22" r="5" fill="none" stroke="var(--orange)" stroke-width="2.5"/><path d="M14 46c0-10 6-16 14-16s14 6 14 16M2 44c0-7 4-12 10-12M54 44c0-7-4-12-10-12" fill="none" stroke="var(--orange)" stroke-width="2.5"/></svg>
  <h3>100% Satisfaction Rating</h3><p>Lorem ipsum dolor sit amet, consectetur adipiscing</p>
</div>
<div class="why-circle" style="left:840px">
  <svg width="56" height="56" viewBox="0 0 56 56"><circle cx="28" cy="22" r="16" fill="none" stroke="var(--orange)" stroke-width="2.5"/><path d="M20 22l6 6 10-12" fill="none" stroke="var(--orange)" stroke-width="2.5"/><path d="M18 36l-4 16 14-6 14 6-4-16" fill="none" stroke="var(--orange)" stroke-width="2.5"/></svg>
  <h3>15-Year Warranty on Water Heater &amp; Parts</h3><p>Lorem ipsum dolor sit amet, consectetur adipiscing</p>
</div>

<!-- LOCATION & TESTIMONIALS -->
<div class="abs display section-title" style="left:108px;top:3268px"><span class="b">Our </span><span class="o">Location</span></div>
<div class="abs" style="left:111px;top:3348px;width:453px;height:356px;background:linear-gradient(135deg,#cfe8d6,#e6f2e8 50%,#d4e9f5)" role="img" aria-label="Map of the service area"></div>
<div class="abs" style="left:128px;top:3366px;padding:12px 16px;background:#fff;box-shadow:0 1px 4px rgba(0,0,0,.3);font-size:14px;font-weight:500;text-decoration:underline;color:#222">View Larger Map</div>

<div class="abs display section-title" style="left:662px;top:3268px"><span class="b">Testim</span><span class="o">onials</span></div>
<p class="abs" style="left:668px;top:3352px;width:425px;font-size:16.5px;line-height:26px;font-style:italic;color:#333">“Lorem ipsum dolor sit amet, consectetur adipiscing elit, sed do eiusmod tempor incididunt ut labore et dolore magna aliqua. Ut enim ad minim veniam, quis nostrud exercitation ullamco laboris nisi ut aliquip ex ea commodo consequat.”</p>
<div class="abs" style="left:666px;top:3504px;width:78px;height:78px;border-radius:50%;background:linear-gradient(135deg,#f3b27a,#e6935a)" role="img" aria-label="Customer portrait"></div>
<div class="abs" style="left:759px;top:3515px;font-size:21px;font-weight:500">John Doe</div>
<div class="abs" style="left:759px;top:3547px;font-size:16px;color:#555">Company name</div>
<svg class="abs" style="left:977px;top:3627px" width="110" height="50" viewBox="0 0 110 50">
  <circle cx="25" cy="25" r="24" fill="#ddd"/><path d="M28 17l-8 8 8 8" stroke="#333" stroke-width="2" fill="none"/>
  <circle cx="84" cy="25" r="24" fill="var(--navy)"/><path d="M81 17l8 8-8 8" stroke="#fff" stroke-width="2" fill="none"/>
</svg>

<!-- CONTACT FORM & FOOTER -->
<svg class="bg-band" style="top:4040px" width="1200" height="741" viewBox="0 0 1200 741">
  <defs><linearGradient id="gFoot" x1="0" y1="0" x2="1" y2="1"><stop offset="0" stop-color="#103f98"/><stop offset="1" stop-color="#1a5bb5"/></linearGradient></defs>
  <polygon points="0,30 600,190 1200,20 1200,741 0,741" fill="var(--orange)"/>
  <polygon points="1200,20 800,130 1200,60" fill="var(--yellow)"/>
  <polygon points="0,90 600,190 1200,70 1200,741 0,741" fill="url(#gFoot)"/>
</svg>
<svg class="abs" style="left:234px;top:3802px" width="734" height="251" viewBox="0 0 734 251">
  <defs><pattern id="dots" width="6" height="6" patternUnits="userSpaceOnUse"><circle cx="2" cy="2" r="1" fill="#ccc"/></pattern></defs>
  <rect width="734" height="251" fill="url(#dots)"/>
</svg>
<div class="abs" style="left:252px;top:3802px;width:696px;height:510px;background:#fff"></div>
<div class="abs display section-title" style="left:0;width:1200px;top:3858px;text-align:center"><span class="b">Get </span><span class="o">in Touch</span></div>
<div class="field" style="left:295px;top:3932px;width:291px;height:50px">Name</div>
<div class="field" style="left:612px;top:3932px;width:291px;height:50px">Email</div>
<div class="field" style="left:295px;top:4002px;width:608px;height:51px">Company</div>
<div class="field" style="left:295px;top:4073px;width:608px;height:133px">Message</div>
<div class="btn btn-blue" style="left:517px;top:4234px;width:166px;height:47px">Submit Now</div>

<div class="abs foot-h" style="left:122px;top:4412px">QUICK LINKS</div>
<ul class="abs foot-links" style="left:122px;top:4462px">
  <li>Home</li><li>Gas Water Heaters</li><li>Electric Water Heaters</li><li>Tankless Water Heaters</li><li>About Us</li><li>Contact Us</li>
</ul>
<div class="abs" style="left:382px;top:4405px;width:1px;height:241px;background:rgba(255,255,255,.6)"></div>
<div class="abs" style="left:779px;top:4405px;width:1px;height:241px;background:rgba(255,255,255,.6)"></div>

<div class="foot-icon" style="left:557px;top:4381px"><svg width="14" height="18" viewBox="0 0 14 18"><path d="M7 0a7 7 0 0 0-7 7c0 5 7 11 7 11s7-6 7-11a7 7 0 0 0-7-7z" fill="#fff"/><circle cx="7" cy="7" r="2.5" fill="var(--orange)"/></svg></div>
<div class="foot-text" style="top:4430px">123, Lorem ipsum dolor sit<br>amet, conse</div>
<div class="foot-icon" style="left:557px;top:4487px"><svg width="18" height="13" viewBox="0 0 18 13"><rect width="18" height="13" rx="2" fill="#fff"/><path d="M1 1l8 6 8-6" stroke="var(--orange)" stroke-width="1.5" fill="none"/></svg></div>
<div class="foot-text" style="top:4533px">info@companyname.com</div>
<div class="foot-icon" style="left:557px;top:4572px"><svg width="16" height="16" viewBox="0 0 24 24"><path d="M4 3c2 9 8 15 17 17l1-5-6-2-3 3c-3-1-6-4-7-7l3-3-2-6z" fill="#fff"/></svg></div>
<div class="foot-text" style="top:4618px">+1 888 888 8888</div>

<div class="abs foot-h" style="left:833px;top:4412px">NEWSLETTER</div>
<p class="abs" style="left:833px;top:4464px;width:270px;font-size:14px;line-height:26px;color:#fff">Lorem ipsum dolor sit amet, consectetur adipiscing elit, sed do eiusmod tempor</p>
<div class="abs" style="left:836px;top:4540px;width:245px;height:45px;background:#fff;border-radius:4px;font-size:13px;color:#555;padding:14px 22px">Email address</div>
<svg class="abs" style="left:1038px;top:4544px" width="38" height="37" viewBox="0 0 38 37"><rect width="38" height="37" rx="3" fill="var(--blue)"/><path d="M10 19l18-8-6 17-3-7z" fill="#fff"/></svg>
<div class="social" style="left:833px"></div>
<div class="social" style="left:869px"></div>
<div class="social" style="left:902px"></div>
<div class="social" style="left:937px"></div>

<div class="abs" style="left:111px;top:4706px;width:978px;height:1px;background:rgba(255,255,255,.6)"></div>
<div class="abs" style="left:111px;top:4730px;font-size:13px;color:#fff">Privacy Policy &nbsp;| &nbsp;Terms &amp; Conditions</div>
<div class="abs" style="left:726px;top:4730px;font-size:13px;color:#fff">© Copyrights 2026 Company Name | All Rights reserved</div>

</body>
</html>
```